Website design for legal tech start up in Switzerland (B2B)

We are for a legal tech start up in Switzerland called KOVA. We have been running since August 2016. This will be our first live website.

We need a website designed and business card design for our start-up in Switzerland. We also need the Web design to be converted into HTML and CSS files.

Function of website:
• To inform potential customers of our services
• Form a key part of our digital marketing and sales footprint.
• Branding

Please find attached logo.
Updates

Project Deadline Extended Reason: Giving us time to review submissions and provide opportunity for more submissions. Added Thursday, February 16, 2017

Project Deadline Extended
Reason: Looking for more idea's not necessarily set on blue and grey colours only.

Target Market(s)

B2B tech powered legal services.

Industry/Entity Type

Legal

Contact Information for Business Card

Lean and slick design.

Coding

Coded - Design and coding required

Number of Pages Required

5+ page

Requirements
Must have
• VERY LEAN AND CLEAN DESIGN!
• We have received many great standard designs, but we are looking for something more out-of-the box: You can get inspiration from these designs: http://www.pixelvane.com/websites/clean/
• Thanks!!
• Easy content management system
• Well structured coding for additional development
• Responsive webpage for all types of devices
• SEO optimized
• Tabs (Home, services, team, careers, blog, contact us)
• Colour scheme complementary to logo
Nice to have
• Look and Design - Approachable, High-tech, Modern
• Easy to add chat bot capability in future
Should not have
• Too busy/ too much clutter
• Not take to long to load

```html
<!DOCTYPE html>
<html lang="en">
<head>
<meta charset="utf-8">
<title>KOVA – Legal Startup Company</title>
<link href="https://fonts.googleapis.com/css2?family=Open+Sans:wght@400;600;700&display=swap" rel="stylesheet">
<style>
:root{
  --navy:#1d3a6b;
  --navy-deep:#16305c;
  --ink:#2b2b2b;
  --text:#6a6a6a;
  --muted:#8a8a8a;
  --line:#e4e6ea;
  --footer-bg:#f3f4f6;
  --white:#ffffff;
}
*{margin:0;padding:0;box-sizing:border-box}
html,body{width:1200px;height:3141px;overflow:hidden}
body{font-family:"Open Sans",Arial,sans-serif;color:var(--text);background:var(--white);position:relative}
a{color:inherit;text-decoration:none}

/* Header */
.site-header{position:absolute;top:0;left:0;width:1200px;height:88px;background:var(--white)}
.brand{position:absolute;left:100px;top:18px;font-size:48px;font-weight:700;letter-spacing:4px;color:var(--ink);line-height:52px}
.main-nav{position:absolute;right:62px;top:0;display:flex;gap:0}
.main-nav a{display:block;height:88px;line-height:88px;padding:0 26px;font-size:14px;color:var(--ink);position:relative}
.main-nav a.active::after{content:"";position:absolute;left:18px;right:18px;bottom:16px;height:3px;background:var(--navy)}

/* Hero */
.hero{position:absolute;top:88px;left:0;width:1200px;height:544px;
  background:linear-gradient(180deg,#8fb0cf 0%,#6d8fb3 35%,#4a6281 62%,#3a4d66 80%,#2f4766 100%)}
.hero-title{position:absolute;top:210px;width:100%;text-align:center;color:var(--white)}
.hero-title .hero-brand{font-size:56px;font-weight:600;letter-spacing:6px;line-height:64px}
.hero-title .hero-tag{font-size:32px;font-weight:700;margin-top:6px}
.dots{position:absolute;display:flex;gap:6px}
.dots span{width:8px;height:8px;border-radius:50%;background:rgba(255,255,255,.55)}
.dots span.on{background:var(--white)}
.hero .dots{left:574px;top:516px}

/* Welcome */
.section-title{font-size:24px;font-weight:700;color:var(--ink);text-align:center;letter-spacing:.5px}
.welcome{position:absolute;top:632px;left:0;width:1200px;height:340px}
.welcome .section-title{margin-top:72px}
.welcome p{width:940px;margin:26px auto 0;text-align:center;font-size:13.5px;line-height:27px}
.btn{display:inline-block;height:40px;line-height:40px;padding:0 30px;border-radius:20px;background:var(--navy);color:var(--white);font-size:12px;text-transform:uppercase}
.btn-row{position:absolute;top:270px;left:0;width:100%;display:flex;justify-content:center;gap:28px}
.btn-row .btn{width:160px;text-align:center;padding:0}

/* Services */
.services{position:absolute;top:1030px;left:0;width:1200px;height:300px}
.service{position:absolute;top:0;width:240px;text-align:center}
.service .icon{width:98px;height:98px;border:1.5px solid var(--navy);border-radius:50%;margin:16px auto 0;display:flex;align-items:center;justify-content:center}
.service h3{font-size:13px;font-weight:700;color:var(--ink);margin-top:28px;text-transform:uppercase}
.service p{font-size:11.5px;line-height:21px;margin-top:14px}
.arrow{position:absolute;top:126px}

/* Careers */
.careers{position:absolute;top:1344px;left:0;width:1200px;height:406px;
  background:linear-gradient(120deg,#2a4a7e 0%,#20427a 40%,#1a3768 100%);color:var(--white);text-align:center}
.careers h2{font-size:24px;font-weight:700;margin-top:104px}
.careers p{width:950px;margin:22px auto 0;font-size:13.5px;line-height:27px;color:#e7ecf5}
.btn-ghost{display:inline-block;margin-top:30px;width:160px;height:40px;line-height:38px;border:1.5px solid var(--white);border-radius:20px;font-size:12px;text-transform:uppercase}

/* Blog */
.blog{position:absolute;top:1750px;left:0;width:1200px;height:518px}
.blog .section-title{margin-top:70px}
.blog .lead{text-align:center;font-size:13px;margin-top:12px}
.post{position:absolute;top:172px;width:330px}
.post h3{font-size:13px;font-weight:700;color:var(--ink);line-height:22px;text-transform:uppercase}
.post .rule{width:44px;height:3px;background:var(--navy);margin:14px 0 18px}
.post p{font-size:12.5px;line-height:22px}
.blog .btn{position:absolute;top:386px;left:512px;width:176px;text-align:center;padding:0}

/* Testimonial */
.testimonial{position:absolute;top:2268px;left:0;width:1200px;height:540px;overflow:hidden}
.testimonial .photo{position:absolute;inset:0;background:linear-gradient(110deg,#f0f0f0 40%,#cfcfcf 65%,#9a9a9a 85%,#c9c9c9 100%)}
.testimonial .panel{position:absolute;inset:0}
.quote{position:absolute;left:0;top:0;width:600px;text-align:center;color:var(--white)}
.quote .mark{margin-top:100px;font-size:70px;font-weight:700;line-height:60px;color:#7b90b6}
.quote p{width:440px;margin:18px auto 0;font-size:13px;line-height:27px}
.quote p + p{margin-top:28px}
.quote .author{margin-top:14px;font-size:13px}
.quote .author b{font-weight:700}
.testimonial .dots{left:280px;top:468px}
.testimonial .dots span{width:6px;height:6px;background:#6f84ab}

/* Footer */
.site-footer{position:absolute;top:2808px;left:0;width:1200px;height:270px;background:var(--footer-bg)}
.fcol{position:absolute;top:46px}
.fcol h4{font-size:13px;font-weight:700;color:var(--navy);text-transform:uppercase;margin-bottom:18px}
.fcol p{font-size:11.5px;line-height:21px}
.fcol ul{list-style:none}
.fcol li{font-size:11.5px;line-height:27px}
.fcol .contact li{display:flex;align-items:center;gap:10px}
.footer-brand{position:absolute;left:102px;top:170px;font-size:44px;font-weight:700;letter-spacing:4px;color:var(--navy)}
.bottom-bar{position:absolute;top:3078px;left:0;width:1200px;height:63px;background:var(--white);font-size:11px;color:var(--muted)}
.bottom-bar .copy{position:absolute;left:102px;top:24px}
.bottom-bar .social{position:absolute;right:70px;top:20px;display:flex;align-items:center;gap:20px}
.bottom-bar .social i{width:12px;height:12px;border-radius:50%;background:var(--navy);display:block}
</style>
</head>
<body>

<header class="site-header">
  <div class="brand">KOVA</div>
  <nav class="main-nav">
    <a href="#" class="active">Home</a>
    <a href="#">Services</a>
    <a href="#">Team</a>
    <a href="#">Careers</a>
    <a href="#">Blog</a>
    <a href="#">Contact us</a>
  </nav>
</header>

<section class="hero" role="img" aria-label="City skyline with tall buildings above a river">
  <div class="hero-title">
    <div class="hero-brand">KOVA</div>
    <div class="hero-tag">LEGAL STARTUP COMPANY</div>
  </div>
  <div class="dots"><span class="on"></span><span></span><span></span><span></span></div>
</section>

<section class="welcome">
  <h2 class="section-title">WELCOME TO KOVA</h2>
  <p>Lorem Ipsum is simply dummy text of the printing and typesetting industry. Lorem Ipsum has been the industry's standard dummy text ever since the 1500s, when an unknown printer took a galley of type and scrambled it to make a type specimen book. It has survived not only five centuries, but also the leap into electronic typesetting, remaining essentially unchanged. It was popularised in the 1960s with the release of Lettraform sheets containing...</p>
  <div class="btn-row">
    <a class="btn" href="#">Read more info</a>
    <a class="btn" href="#">Contact here!</a>
  </div>
</section>

<section class="services">
  <svg class="arrow" style="left:44px" width="14" height="24" viewBox="0 0 14 24"><path d="M12 2 2 12l10 10" fill="none" stroke="#b5b9c0" stroke-width="1.5"/></svg>
  <svg class="arrow" style="left:1142px" width="14" height="24" viewBox="0 0 14 24"><path d="M2 2l10 10L2 22" fill="none" stroke="#b5b9c0" stroke-width="1.5"/></svg>

  <div class="service" style="left:86px">
    <div class="icon"><svg width="48" height="40" viewBox="0 0 48 40" fill="none" stroke="#1d3a6b" stroke-width="1.6"><path d="M24 4v32M10 36h28M8 10h32M8 10l-6 14h12zM40 10l-6 14h12z"/></svg></div>
    <h3>Criminal Law</h3>
    <p>Lorem Ipsum is simply dummy text of the printing and typesetting industry. Lorem Ipsum has been the industry</p>
  </div>
  <div class="service" style="left:348px">
    <div class="icon"><svg width="40" height="48" viewBox="0 0 40 48" fill="none" stroke="#1d3a6b" stroke-width="1.6"><circle cx="12" cy="8" r="5"/><circle cx="28" cy="8" r="5"/><path d="M6 44V18h12v26M22 44V18h12v26"/></svg></div>
    <h3>Family Law</h3>
    <p>Lorem Ipsum is simply dummy text of the printing and typesetting industry. Lorem Ipsum has been the industry</p>
  </div>
  <div class="service" style="left:610px">
    <div class="icon"><svg width="40" height="44" viewBox="0 0 40 44" fill="none" stroke="#1d3a6b" stroke-width="1.6"><rect x="6" y="4" width="18" height="38"/><rect x="24" y="18" width="12" height="24"/><path d="M11 12h3M16 12h3M11 20h3M16 20h3M11 28h3M16 28h3"/></svg></div>
    <h3>Corporate &amp; Commercial</h3>
    <p>Lorem Ipsum is simply dummy text of the printing and typesetting industry. Lorem Ipsum has been the industry</p>
  </div>
  <div class="service" style="left:872px">
    <div class="icon"><svg width="44" height="44" viewBox="0 0 44 44" fill="none" stroke="#1d3a6b" stroke-width="1.6"><rect x="4" y="14" width="16" height="26"/><rect x="20" y="6" width="18" height="34"/><path d="M9 22h6M9 30h6M25 14h8M25 22h8M25 30h8"/></svg></div>
    <h3>Building &amp; Construction</h3>
    <p>Lorem Ipsum is simply dummy text of the printing and typesetting industry. Lorem Ipsum has been the industry</p>
  </div>
</section>

<section class="careers" role="img" aria-label="Navy-tinted photo of a hand signing a document">
  <h2>CAREERS</h2>
  <p>Lorem Ipsum is simply dummy text of the printing and typesetting industry. Lorem Ipsum has been the industry's standard dummy text ever since the 1500s, when an unknown printer took a galley of type and scrambled it to make a type specimen book. It has survived not only five centuries, but also the leap into electronic typesetting...</p>
  <a class="btn-ghost" href="#">Read more info</a>
</section>

<section class="blog">
  <h2 class="section-title">BLOG POSTS</h2>
  <p class="lead">Lorem Ipsum is simply dummy text of the printing and typesetting industry. Lorem Ipsum has been the industry</p>
  <article class="post" style="left:100px">
    <h3>Lorem Ipsum is simply dummy text<br>of the printing</h3>
    <div class="rule"></div>
    <p>Lorem Ipsum is simply dummy text of the printing and typesetting industry. Lorem Ipsum has been the industry's standard dummy text ever since the 1500s</p>
  </article>
  <article class="post" style="left:468px">
    <h3>Lorem Ipsum is simply dummy text<br>of the printing</h3>
    <div class="rule"></div>
    <p>Lorem Ipsum is simply dummy text of the printing and typesetting industry. Lorem Ipsum has been the industry's standard dummy text ever since the 1500s</p>
  </article>
  <article class="post" style="left:836px">
    <h3>Lorem Ipsum is simply dummy text<br>of the printing</h3>
    <div class="rule"></div>
    <p>Lorem Ipsum is simply dummy text of the printing and typesetting industry. Lorem Ipsum has been the industry's standard dummy text ever since the 1500s</p>
  </article>
  <a class="btn" href="#">View more posts</a>
</section>

<section class="testimonial">
  <div class="photo" role="img" aria-label="Black and white photo of a smiling businessman giving a thumbs up with colleagues behind him"></div>
  <svg class="panel" width="1200" height="540" viewBox="0 0 1200 540"><polygon points="0,0 540,0 806,540 0,540" fill="#1d3a6b"/></svg>
  <div class="quote">
    <div class="mark">&#8220;</div>
    <p>Lorem Ipsum is simply dummy text of the printing and typesetting industry. Lorem Ipsum has been the industry's standard dummy text ever since the 1500s, when an unknown printer took a galley of type and scrambled.</p>
    <p>It was popularised in the 1960s with the release of Lettraform sheets containing Lorem Ipsum passages, and more recently with desktop publishing software.</p>
    <div class="author"><b>Marcus Heller</b> - Business man -</div>
  </div>
  <div class="dots"><span></span><span></span><span></span></div>
</section>

<footer class="site-footer">
  <div class="fcol" style="left:102px;width:330px">
    <h4>Privacy Policy</h4>
    <p>Lorem Ipsum is simply dummy text of the printing and typesetting industry. Lorem Ipsum has been the industry's standard dummy text ever since the 1500s...</p>
  </div>
  <div class="footer-brand">KOVA</div>
  <div class="fcol" style="left:512px">
    <h4>Welcome</h4>
    <ul><li>Home</li><li>Services</li><li>Team</li><li>Careers</li><li>Blog</li><li>Contact us</li></ul>
  </div>
  <div class="fcol" style="left:700px">
    <h4>Information</h4>
    <ul><li>Terms &amp; Conditions</li><li>Privacy policy</li><li>Disclaimer</li><li>Sitemap</li></ul>
  </div>
  <div class="fcol" style="left:908px">
    <h4>Contact Info</h4>
    <p>120 Street name, City name,<br>Country name : 958669</p>
    <ul class="contact" style="margin-top:4px">
      <li><svg width="12" height="12" viewBox="0 0 12 12"><path d="M2 1h3l1 3-2 1a7 7 0 0 0 3 3l1-2 3 1v3c-6 0-9-3-9-9z" fill="#1d3a6b"/></svg>( 555 ) 210 - 4471</li>
      <li><svg width="12" height="12" viewBox="0 0 12 12"><rect x="3" y="1" width="6" height="3" fill="#1d3a6b"/><rect x="1" y="4" width="10" height="5" fill="#1d3a6b"/><rect x="3" y="8" width="6" height="3" fill="#1d3a6b"/></svg>( 555 ) 210 - 4471</li>
      <li><svg width="12" height="12" viewBox="0 0 12 12"><rect x="1" y="2" width="10" height="8" fill="#1d3a6b"/><path d="M1 2l5 4 5-4" fill="none" stroke="#fff" stroke-width="1"/></svg>info@kova.com</li>
    </ul>
  </div>
</footer>

<div class="bottom-bar">
  <div class="copy">© 2017, Kova. All rights reserved</div>
  <div class="social">
    <span>Connect with our social network :</span>
    <i></i><i></i><i></i><i></i><i></i>
  </div>
</div>

</body>
</html>
```